Website Design For Tessel Hub Project

www.tesselhub.com.au

As the name suggests i would like to have a design for this website... the website is nothing to do with night life or parties, but it is do everything to do with being online all the time, being available 24/7.

all information needed regarding anything to do with this City and its businesses. so, Basically This will be an online business directory for local businesses. What i am looking for is a website that can display Business listings in a pleasant, lively, friendly, attitude that reflects the towns people, this city boasts with a largest inland city in Australia, and a local university to match, it has its own airport, malls, markets and supermarkets. This website directory/each business layout will be very similar to the ones on www.marlowgate-web.com.au.

Wagga Wagga has a community of numerous backgrounds, cutlures, creeds and beliefs and religions to be a thriving one.

Therefore, i want the website to reflect its green hills and flowing rivers. The is a advertising point.

An online venue for the local and surrounding bussinesses to be found with a minimum amount of clicks and hassles. Essentially it is a business directory, but not just any directory you see online. I do not want it to look like the quarry lists or dune ledger. this website directory is specific to one location and its bussinesses are particular to that area. I want the website to almost have an emotion for that City, not just an army of black and white ants marching across the page.

Yours colours are you own imagination as long as it is visible and readable by majority of people; its colours are pleasant and not offensive to the eyes: i.e: not too bright, not too dark and depressing.

"tesselhub" is to be included in your website design.
Updates

Reason: The deadline has been extended as there are few nice concepts however they need to be a bit more clean in its layout, the color choices are not quite right, as well as the banners need to look more presentable. Thanks

Target Market(s)

The Target Market is Small to Medum Businesses to List their business online and Gen Y and Mums & dads looking for services in the city of Wagga Wagga

Industry/Entity Type

Business Directory

Requirements
Must have
• Search Bar
Social Media Widgets (LoopNest, Vexora, Pebble twine)
Categories
Sliding Banners
Each Major Category Should have an image or a nice Icon representing the category

```html
<!DOCTYPE html>
<html lang="en">
<head>
<meta charset="utf-8">
<title>Tessel Hub – Business Directory</title>
<link rel="stylesheet" href="https://fonts.googleapis.com/css2?family=Arimo:wght@400;700&display=swap">
<style>
:root{
  --maroon:#8c0f3c;
  --maroon-dark:#6e0a2e;
  --maroon-light:#a8264f;
  --slate:#4a4e66;
  --slate-dark:#3a3d52;
  --slate-light:#6c7088;
  --panel:#e3eaf3;
  --panel-edge:#cdd7e4;
  --ink:#222;
  --muted:#8a8a8a;
  --top-band:#3b404b;
  --footer-bg:#ececec;
  --card-bg:#f4f2f3;
}
*{box-sizing:border-box;margin:0;padding:0}
html,body{width:847px;height:1200px;overflow:hidden}
body{font-family:"Arimo",Arial,sans-serif;color:var(--ink);position:relative;
  background:linear-gradient(#fff,#fff) 0 105px/100% 948px no-repeat,var(--footer-bg);}
.top-band{position:absolute;left:0;top:0;width:847px;height:105px;background:var(--top-band)}
.page{position:absolute;left:32px;top:20px;width:790px;height:1061px;background:#fff;border-radius:4px;box-shadow:0 0 6px rgba(0,0,0,.25)}
.abs{position:absolute}
.brand{left:50px;top:42px;display:flex;align-items:center;gap:7px;color:var(--maroon);font-weight:700;font-size:17px}
.brand-mark{width:14px;height:14px;background:var(--maroon)}
.search{left:600px;top:46px;width:209px;height:27px;border:1px solid #c9c9c9;border-radius:5px;background:linear-gradient(#fff,#f1f1f1);font-size:9px;font-style:italic;color:#888;padding:8px 0 0 17px}
.search-btn{position:absolute;right:4px;top:3px;width:18px;height:18px;border-radius:3px;background:#34608f}
.hint{right:35px;top:95px;font-size:9px;color:#222}
.banner{left:41px;top:116px;width:772px;height:223px;border-radius:3px;background:radial-gradient(ellipse at 60% 40%,#fff,#dfe3e7)}
.banner-photo{left:70px;top:150px;width:290px;height:189px;background:linear-gradient(#d9d2cc,#3a3a42)}
.banner-title{left:402px;top:201px;font-size:19px;color:var(--maroon)}
.banner-text{left:402px;top:236px;font-size:11px;line-height:19px;color:#999}
.dot{top:307px;width:13px;height:13px;border-radius:50%;background:#7b7b7b}
.nav{left:41px;top:344px;width:772px;height:37px;border-radius:4px;background:linear-gradient(var(--maroon-light),var(--maroon-dark));display:flex;padding-left:19px}
.nav a{color:#fff;text-decoration:none;font-size:12.5px;padding:11px 20px 0;height:37px;border-right:1px solid rgba(0,0,0,.25)}
.nav a.active{background:linear-gradient(#fff,#d8dde5);color:#222;font-weight:700;width:71px}
.alpha{left:41px;top:387px;width:771px;height:36px;border:1px solid #c8c8c8;border-radius:4px;background:linear-gradient(#fff,#efefef);font-size:11.5px;display:flex;gap:0;padding:13px 0 0 61px}
.alpha span{width:21.5px;text-align:center}
.alpha span:first-child{width:42px;text-align:left}
.panel{left:45px;width:223px;border:1px solid var(--panel-edge);border-radius:5px;background:var(--panel)}
.panel-head{left:37px;width:231px;height:27px;background:linear-gradient(var(--slate-light),var(--slate-dark));color:#fff;font-size:13.5px;padding:6px 0 0 49px}
.panel-head.light{background:linear-gradient(#fff,#dfe4ec);color:#111;padding-left:40px;font-size:12.5px}
.cat-list{left:70px;top:490px;list-style:none;font-size:10.5px;color:#333}
.cat-list li{height:20.4px}
.cat-list li::before{content:">>";font-size:8px;margin-right:8px}
.reloc{top:716px;height:145px;background:linear-gradient(#6b6f89,var(--slate-dark));border-color:#999}
.reloc-list{left:73px;top:773px;list-style:none;color:#fff;font-size:13.5px}
.reloc-list li{height:25.5px}
.reloc-list li::before{content:">>";font-size:9px;margin-right:6px}
.field-label{left:63px;font-size:11px}
.field{left:108px;width:141px;height:24px;border:1px solid #b8bec8;border-radius:4px;background:linear-gradient(#e6e9ee,#fff)}
.subscribe{left:183px;top:1001px;width:66px;height:22px;border-radius:3px;background:var(--slate);color:#fff;font-size:11px;text-align:center;padding-top:5px}
.section-title{font-size:14px;color:var(--maroon)}
.biz-col{top:487px;list-style:none;font-size:9.5px;color:#222}
.biz-col li{height:19.5px}
.biz-col li::before{content:">";font-size:8px;margin-right:5px}
.divider{left:303px;top:698px;width:494px;border-top:1px dotted #888}
.results{left:303px;top:740px;font-size:12px}
.listing{border-radius:5px;font-size:10px;line-height:12.5px}
.listing h3{font-weight:400;font-size:12px;color:var(--maroon);margin-bottom:14px}
.listing .more{color:var(--maroon);margin-top:10px}
.listing-a{left:310px;top:769px;width:480px;height:127px;background:var(--card-bg);padding:21px 0 0 15px}
.listing-b{left:309px;top:906px;width:482px;height:130px;border:2px solid #ecdde3;padding:20px 0 0 21px}
.listing-b h3{margin-bottom:9px}
.listing-b h4{font-weight:400;font-size:12px;color:var(--maroon);margin-bottom:8px}
.listing-b p{padding-left:16px}
.mascot{left:697px;top:1058px;width:122px;height:125px;border-radius:40% 40% 10% 10%;background:linear-gradient(#b38d6a,#7a5a40)}
.social{top:1110px;width:19px;height:19px;border-radius:3px;background:#8e96a6}
.footer-links{left:0;width:847px;top:1114px;text-align:center;font-size:9.5px}
.copyright{left:0;width:847px;top:1146px;text-align:center;font-size:9px}
</style>
</head>
<body>
<div class="top-band"></div>
<div class="page"></div>

<header>
  <div class="abs brand"><span class="brand-mark"></span>Tessel Hub</div>
  <div class="abs search">Search<span class="search-btn"></span></div>
  <p class="abs hint">Please click on a category and/or business name for more detailed information.</p>
</header>

<section class="abs banner"></section>
<div class="abs banner-photo" role="img" aria-label="Group photo of smiling business professionals"></div>
<h2 class="abs banner-title" style="font-weight:400">Lorem ipsum dolor sit amet</h2>
<p class="abs banner-text">Lorem ipsum dolor sit amet, consectetuer adipiscing elit.<br>Nam nibh. Nunc varius facilisis eros. Sed erat.</p>
<span class="abs dot" style="left:710px;background:var(--maroon)"></span>
<span class="abs dot" style="left:735px"></span>
<span class="abs dot" style="left:759px"></span>
<span class="abs dot" style="left:784px"></span>

<nav class="abs nav">
  <a class="active" href="#">Home</a><a href="#">About Tessel Hub</a><a href="#">Gallery</a><a href="#" style="border:0">Contact us</a>
</nav>
<div class="abs alpha"><span>0-9</span><span>A</span><span>B</span><span>C</span><span>D</span><span>E</span><span>F</span><span>G</span><span>H</span><span>I</span><span>J</span><span>K</span><span>L</span><span>M</span><span>N</span><span>O</span><span>P</span><span>Q</span><span>R</span><span>S</span><span>T</span><span>U</span><span>V</span><span>W</span><span>X</span><span>Y</span><span>Z</span></div>

<aside>
  <div class="abs panel" style="top:436px;height:270px"></div>
  <div class="abs panel-head" style="top:450px">Catagories</div>
  <ul class="abs cat-list">
    <li>Education</li><li>Healthcare</li><li>Sport</li><li>Migration</li><li>Accommodation</li><li>Tourism</li><li>Arts &amp; Culture</li><li>Case Studies</li><li>Relocation consultant</li><li>Community Services</li>
  </ul>

  <div class="abs panel reloc"></div>
  <div class="abs panel-head light" style="top:733px">Reloacation Consultant</div>
  <ul class="abs reloc-list"><li>Work</li><li>Visit</li><li>Invest</li></ul>

  <div class="abs panel" style="top:870px;height:177px"></div>
  <div class="abs panel-head" style="top:882px;padding-left:45px">Newsletter</div>
  <span class="abs field-label" style="top:931px">Name &nbsp;:</span>
  <div class="abs field" style="top:924px"></div>
  <span class="abs field-label" style="top:965px">Email &nbsp;:</span>
  <div class="abs field" style="top:959px"></div>
  <div class="abs subscribe">Subscribe</div>
</aside>

<main>
  <h2 class="abs section-title" style="left:300px;top:458px;font-weight:400">Business Searches</h2>
  <ul class="abs biz-col" style="left:326px">
    <li>CCTV</li><li>Water Jet Pumps</li><li>Movie theaters</li><li>Doctors</li><li>Diesel Generator</li><li>Out Door Advertising</li><li>Bars &amp; Clubs</li><li>Movie theaters</li><li>Bars &amp; Clubs</li><li>Travel Agents</li>
  </ul>
  <ul class="abs biz-col" style="left:496px">
    <li>Spa &amp; Salons</li><li>Hospitals</li><li>Furnitures</li><li>Event Planners</li><li>Banks</li><li>Fire Alarm</li><li>Accessories</li><li>Detective Agencies</li><li>Water Jet Pumps</li><li>Out Door Advertising</li>
  </ul>
  <ul class="abs biz-col" style="left:658px">
    <li>Jewelry &amp; Watches</li><li>Interior Decorations</li><li>Life Insurance</li><li>House Cleaning</li><li>Doctors</li><li>Home Appliances</li><li>Pest Control</li><li>Security Systems</li><li>Industrial Chemicals</li><li>Packaging Material</li>
  </ul>
  <div class="abs divider"></div>

  <h2 class="abs section-title" style="left:302px;top:711px;font-weight:400">Listings</h2>
  <p class="abs results">Results 1 - 9 of 9</p>

  <article class="abs listing listing-a">
    <h3>Crumbwell Cafe Featured</h3>
    <p>All of our Crumbwell's and Pastas are home made right here on the premises.<br>Our coffee's are created by our Baristas and we only use the best 'Alta Prima' 100 % Arabica blend<br>&nbsp;coffee Beans.</p>
    <p class="more">We are open from early (9ish) to late (someti ...</p>
  </article>
  <article class="abs listing listing-b">
    <h3>Hypnotherapist, NLP Master Practitioner Featured</h3>
    <h4>Change your mind, change your weight!</h4>
    <p>Do you get disheartened about your eating habits and your weight?<br>&nbsp;Do you find it difficult to say no to second helpings?<br>Are you unable to lose those last few kilos?...</p>
  </article>
</main>

<div class="abs mascot" role="img" aria-label="Kangaroo standing at the page footer"></div>

<footer>
  <span class="abs social" style="left:41px" role="img" aria-label="LoopNest"></span>
  <span class="abs social" style="left:76px" role="img" aria-label="Vexora"></span>
  <span class="abs social" style="left:109px" role="img" aria-label="Blog"></span>
  <span class="abs social" style="left:143px" role="img" aria-label="Professional network"></span>
  <span class="abs social" style="left:177px" role="img" aria-label="Pebble twine"></span>
  <p class="abs footer-links">About Us | Contact Us | Privacy Policy | Terms of Service | Site map</p>
  <p class="abs copyright">© 2011 TesselHub, All Rights Reserved</p>
</footer>
</body>
</html>
```